Top header for website

Header for website Size is 1000px x 120px
I have CS5 so will need the source files photoshop, illustrator etc, so I can change text and photos.
Photos attached, includes example header and screenshot of eg site
Brief:
I need a website header for golfers where I can change the photos and their name.
The header needs to have these things.
- pictures of the golfer (use from pics attached)
- Their name
- Also under there name is smaller text I need a line of text you can just say "Offical Website" in your e.g to me
so for example you should have
Colin Perrault
Offical Website
And some photos that are blended with some nice golf background or some grass or other ideas that you come up with that will look better than mine I'm sure :)
Size is 1000px x 120px
It needs to look professional and blend in nicely. I don't mind how many photos are used maybe 1-4?
The text needs to look professional too but not boring.
The header you create will be used on a website for a Professional Golfer (tour pro) their job is golf, their website needs to showcase them and promote them as best as possible.
As I said above I will need to swap photos easily and edit the text so will need the source files.
So a important point here. I guess there is no need to blend or do anything to the photos you add as I will actually need to change the photos and just need a simple template that I can swap photos and edit their name.
Ultimately I would like 3 versions of the header done and source files for all 3 so I can give them(the golfers) a choice of header type.
See how you go.
Remember that the header must have the ability for me to easily swap images and of course change the text.
My goal is to use the same header for each golfer but obviously with their images and their name.
I have CS5 so will need the source files photoshop, illustrator etc
2 example headers are attached to show you my attempts :) Please do something better.
I don't want any flash.

```html
<!DOCTYPE html>
<html lang="en">
<head>
<meta charset="utf-8">
<title>Colin Perrault – Official Website</title>
<link href="https://fonts.googleapis.com/css2?family=Open+Sans:wght@300;400;700&family=PT+Sans:wght@400;700&display=swap" rel="stylesheet">
<style>
  :root{
    --backdrop:#3b4147;
    --page:#f3f5f6;
    --nav-top:#4c9bf7;
    --nav-bottom:#1b5fe6;
    --accent:#2f74e0;
    --text:#2a2a2a;
    --muted:#555;
    --rule:#dfe2e4;
    --cell:#e8ebec;
    --cell-head:#dde2e2;
    --button:#eceeef;
    --button-line:#c6cacd;
    --white:#ffffff;
  }
  *{margin:0;padding:0;box-sizing:border-box}
  html,body{width:1200px;height:818px;overflow:hidden}
  body{background:var(--backdrop);font-family:"PT Sans",sans-serif;color:var(--text);position:relative}
  .page{position:absolute;left:44px;top:37px;width:1108px;height:800px;background:var(--page)}
  .site-header{position:absolute;left:0;top:0;width:1108px;height:135px;
    background:linear-gradient(90deg,#151515 0%,#1d211c 30%,#262b24 60%,#1a1a1a 80%,#151515 100%)}
  .header-thumb{position:absolute;left:14px;top:11px;width:178px;height:108px;border:3px solid var(--white);
    background:linear-gradient(135deg,#3d4a2e 0%,#6b5a44 45%,#c7b9a6 70%,#2f3a27 100%)}
  .site-name{position:absolute;left:211px;top:28px;font-family:"Open Sans",sans-serif;font-weight:300;
    font-size:44px;line-height:1;color:var(--white);letter-spacing:.5px;text-transform:uppercase}
  .site-tagline{position:absolute;left:211px;top:79px;font-family:"Open Sans",sans-serif;font-weight:700;
    font-size:16px;color:var(--white);text-transform:uppercase}
  .main-nav{position:absolute;left:0;top:135px;width:1108px;height:65px;
    background:linear-gradient(180deg,var(--nav-top),var(--nav-bottom))}
  .main-nav a{position:absolute;top:14px;font-size:16px;color:var(--white);text-decoration:none;text-transform:uppercase}
  .slider{position:absolute;left:24px;top:223px;width:740px;height:334px;background:var(--white);border:1px solid var(--rule)}
  .slide{position:absolute;left:11px;top:12px;width:717px;height:309px;
    background:linear-gradient(180deg,#3f5a2e 0%,#55703c 40%,#cdd3cf 62%,#e4e7e5 100%)}
  .slider-arrow{position:absolute;top:367px;width:34px;height:36px}
  .section-title{position:absolute;font-size:15px;color:var(--accent)}
  .section-rule{position:absolute;height:2px;background:var(--accent)}
  .article{position:absolute;left:24px;top:644px;width:740px;height:170px;background:var(--white);border:1px solid var(--rule)}
  .article h2{position:absolute;left:11px;top:22px;font-weight:400;font-size:22px;color:#222}
  .article .date{position:absolute;left:11px;top:67px;font-size:12px;color:var(--muted)}
  .article .excerpt{position:absolute;left:11px;top:108px;font-size:12px;color:var(--muted)}
  .article .line{position:absolute;left:11px;width:717px;height:1px;background:var(--rule)}
  .like-box{position:absolute;left:786px;top:276px;display:flex;align-items:center;gap:8px;font-size:11px;color:#333}
  .like-btn{padding:4px 8px;border:1px solid var(--button-line);background:var(--button);color:#333}
  .scores{position:absolute;left:787px;top:380px;width:297px;border-spacing:3px;font-size:12px;color:#333}
  .scores th{background:var(--cell-head);font-weight:400;text-transform:uppercase;color:#666;height:20px;font-size:11px}
  .scores td{background:var(--cell);vertical-align:top;padding:6px 6px;line-height:15px;height:64px}
  .scores td.pos,.scores td.score{text-align:center}
</style>
</head>
<body>
<div class="page">
  <header class="site-header" role="img" aria-label="Blended photos of the golfer on course">
    <div class="header-thumb" role="img" aria-label="Portrait photo of the golfer"></div>
    <div class="site-name">Colin Perrault</div>
    <div class="site-tagline">Offical Website</div>
  </header>

  <nav class="main-nav">
    <a style="left:66px">Home</a><a style="left:160px">About</a><a style="left:260px">News</a>
    <a style="left:353px">Results</a><a style="left:463px">Schedule</a><a style="left:589px">Gallery</a>
    <a style="left:702px">Blog</a><a style="left:791px">Contact</a>
  </nav>

  <div class="slider">
    <div class="slide" role="img" aria-label="Photo of the golfer teeing off in front of spectators"></div>
  </div>
  <svg class="slider-arrow" style="left:6px" viewBox="0 0 34 36"><rect width="34" height="30" fill="#1f66e0"/><path d="M0 30 L8 36 L8 30Z" fill="#0d3e9a"/><path d="M20 7 L12 15 L20 23" stroke="#fff" stroke-width="4" fill="none"/></svg>
  <svg class="slider-arrow" style="left:746px" viewBox="0 0 34 36"><rect width="34" height="30" fill="#1f66e0"/><path d="M34 30 L26 36 L26 30Z" fill="#0d3e9a"/><path d="M14 7 L22 15 L14 23" stroke="#fff" stroke-width="4" fill="none"/></svg>

  <div class="section-title" style="left:22px;top:590px">Latest Articles</div>
  <div class="section-rule" style="left:22px;top:620px;width:742px"></div>

  <article class="article">
    <h2>Kestrel Masters</h2>
    <div class="line" style="top:66px"></div>
    <div class="date">Jan - 11 - 2013</div>
    <div class="line" style="top:94px"></div>
    <div class="excerpt">testing new post</div>
  </article>

  <div class="section-title" style="left:786px;top:233px">Fanpage</div>
  <div class="section-rule" style="left:786px;top:263px;width:299px"></div>
  <div class="like-box"><span class="like-btn">Like</span><span>10 people like this.</span></div>

  <div class="section-title" style="left:786px;top:335px">Latest Scores</div>
  <div class="section-rule" style="left:786px;top:365px;width:299px"></div>

  <table class="scores">
    <colgroup><col style="width:116px"><col style="width:44px"><col style="width:63px"><col style="width:65px"></colgroup>
    <tr><th>Tournament</th><th>Pos</th><th>Score</th><th>Money</th></tr>
    <tr><td>Coastal Pro Championship Nov 29 - Dec 02, 2012</td><td class="pos">35</td><td class="score">69-75-72-71 287 (-1)</td><td>$850</td></tr>
    <tr><td>2012 Harbour Motors Bay Open Nov 22 - Dec 25, 2012</td><td class="pos">56</td><td class="score">79-72-76-70 297 (+9)</td><td>$914.4</td></tr>
    <tr><td>Kestrel Masters Nov 15 - Nov 18, 2012</td><td class="pos">CUT</td><td class="score">77-77-- 154 (+10)</td><td></td></tr>
    <tr><td style="height:80px">Brookfield Bean House Coffee Pro-Am Oct 3 - Oct 4, 2012</td><td class="pos">6</td><td class="score">68-67 135 (-3)</td><td>$669.4</td></tr>
    <tr><td>Southern Pro-Am Championship Mar 29 - Apr 1, 2012</td><td class="pos">CUT</td><td class="score">76-71 147 (+3)</td><td></td></tr>
  </table>
</div>
</body>
</html>
```